Web Design Project for SEARCH ENGINE !

We need a website design for torrents search engine.

The Website will be www.Qentrova.com

Qentrova is a a search engine for torrents.
Qentrova search and index torrents results from all torrents sites.

We will need:
Logo
WebSite Design
slogen (optional)

we need only PSDs - no codded pages are needed !

Design to the following screen Size & resolution: 1024 x 768

***PLEASE DOWNLOAD ATTACHED FILE !

```html
<!DOCTYPE html>
<html lang="en">
<head>
<meta charset="utf-8">
<title>Qentrova — Torrents Search Engine</title>
<link href="https://fonts.googleapis.com/css2?family=Jost:wght@400;500;600&family=Arimo:wght@400&display=swap" rel="stylesheet">
<style>
  :root {
    --frame: #ffffff;
    --bar-top: #3a3a3a;
    --bar-bottom: #121212;
    --ink-light: #f2f2f2;
    --green: #2fa043;
    --gray-text: #5b5b5b;
    --field-text: #3a3a3a;
    --btn: #1b1b1b;
  }
  * { box-sizing: border-box; margin: 0; padding: 0; }
  html, body { width: 1200px; height: 896px; overflow: hidden; background: var(--frame); }
  body { font-family: "Jost", sans-serif; position: relative; }

  .stage {
    position: absolute; left: 8px; top: 5px; width: 1185px; height: 884px;
    background: radial-gradient(ellipse 60% 55% at 50% 55%, #fbfbfb 0%, #e6e6e6 45%, #c4c4c4 100%);
  }
  .top-bar, .footer-bar {
    position: absolute; left: 0; width: 100%;
    background: linear-gradient(var(--bar-top), var(--bar-bottom));
    color: var(--ink-light);
  }
  .top-bar { top: 0; height: 34px; }
  .top-bar-inner {
    position: absolute; left: 247px; top: 0; height: 34px;
    display: flex; align-items: center; white-space: nowrap;
  }
  .main-nav { display: flex; align-items: center; font-size: 14px; }
  .main-nav a { color: var(--ink-light); text-decoration: none; }
  .main-nav a.is-active { color: var(--green); }
  .main-nav .sep { margin: 0 9px; }
  .lang-select {
    position: relative; margin-left: 60px; width: 70px; height: 22px;
    background: var(--green); color: #fff; font-size: 13px;
    display: flex; align-items: center; padding-left: 8px;
  }
  .lang-select svg { position: absolute; right: 8px; top: 8px; }

  .brand {
    position: absolute; left: 0; width: 100%; top: 182px;
    display: flex; flex-direction: column; align-items: center;
  }
  .brand-row { display: flex; align-items: center; gap: 10px; }
  .brand-dot { width: 52px; height: 52px; border-radius: 50%; background: var(--green); }
  .brand-name { font-size: 64px; font-weight: 600; color: var(--gray-text); line-height: 1; }
  .brand-tagline { font-size: 20px; color: var(--gray-text); margin-top: 2px; letter-spacing: 0.3px; }

  .search-bar {
    position: absolute; left: 187px; top: 416px; width: 810px; height: 33px;
    background: linear-gradient(90deg, #9d9d9d, #bdbdbd 50%, #a7a7a7);
  }
  .search-query { position: absolute; left: 8px; top: 5px; font-family: "Arimo", sans-serif; font-size: 19px; color: var(--field-text); }
  .search-button {
    position: absolute; right: 0; top: 0; width: 65px; height: 33px; background: var(--btn);
    color: #fff; font-size: 11px; display: flex; align-items: center; justify-content: center; gap: 4px;
  }
  .sites-include {
    position: absolute; right: 188px; top: 455px; font-size: 12px; color: #333;
    display: flex; align-items: center; gap: 5px;
  }
  .check { width: 11px; height: 11px; border: 1px solid #666; background: #fff; display: inline-block; position: relative; flex: none; }
  .check svg { position: absolute; left: 0; top: 0; }

  .login-panel {
    position: absolute; left: 511px; top: 342px; width: 163px; height: 198px;
    background: linear-gradient(#ffffff, #f1f1f1 80%, #d9d9d9);
    box-shadow: 0 0 5px rgba(0,0,0,0.35);
    font-family: "Arimo", sans-serif; color: #444;
  }
  .panel-tab {
    position: absolute; left: 46px; top: 1px; width: 70px; height: 24px; background: var(--btn);
    color: #fff; font-family: "Jost", sans-serif; font-size: 15px;
    display: flex; align-items: center; justify-content: center;
  }
  .panel-close { position: absolute; right: 6px; top: 7px; }
  .field-label { position: absolute; left: 12px; font-size: 12px; }
  .field-input { position: absolute; left: 12px; width: 138px; height: 17px; border: 1px solid #8a8a8a; background: #fff; }
  .option { position: absolute; left: 12px; display: flex; align-items: center; gap: 8px; font-size: 7px; white-space: nowrap; }
  .option a { color: var(--green); text-decoration: none; }
  .submit-button {
    position: absolute; left: 46px; top: 178px; width: 70px; height: 24px; background: var(--btn);
    color: #fff; font-family: "Jost", sans-serif; font-size: 14px;
    display: flex; align-items: center; justify-content: center;
  }

  .social-links { position: absolute; left: 528px; top: 793px; display: flex; gap: 20px; }
  .social-links span { width: 29px; height: 28px; border-radius: 3px; display: block; }
  .social-feed { background: #d9732a; }
  .social-birds { background: #8fbdd3; }
  .social-book { background: #3a5f9c; }

  .footer-bar { top: 849px; height: 35px; display: flex; align-items: center; justify-content: center; font-size: 13px; white-space: nowrap; }
  .footer-bar a { color: var(--green); text-decoration: none; }
</style>
</head>
<body>
<div class="stage">
  <header class="top-bar">
    <div class="top-bar-inner">
      <nav class="main-nav">
        <a class="is-active" href="#">HOME</a><span class="sep">|</span>
        <a href="#">ABOUT US</a><span class="sep">|</span>
        <a href="#">TORRENT SEARCH</a><span class="sep">|</span>
        <a href="#">SITE SEARCH</a><span class="sep">|</span>
        <a href="#">HELP</a><span class="sep">|</span>
        <a href="#">LOGIN</a><span class="sep">|</span>
        <a href="#">SIGNIN</a>
      </nav>
      <div class="lang-select">English
        <svg width="8" height="6" viewBox="0 0 8 6"><path d="M0 0h8L4 6z" fill="#fff"/></svg>
      </div>
    </div>
  </header>

  <div class="brand">
    <div class="brand-row">
      <span class="brand-dot"></span>
      <span class="brand-name">Qentrova</span>
    </div>
    <div class="brand-tagline">TORRENTS SEARCH ENGINE</div>
  </div>

  <div class="search-bar">
    <span class="search-query">starfall protocol 2</span>
    <div class="search-button">
      <svg width="10" height="10" viewBox="0 0 10 10"><circle cx="6" cy="4" r="3" fill="none" stroke="#fff" stroke-width="1.4"/><path d="M4 6L1 9" stroke="#fff" stroke-width="1.6"/></svg>
      SEARCH
    </div>
  </div>
  <div class="sites-include">Sites search include
    <span class="check"><svg width="10" height="10" viewBox="0 0 10 10"><path d="M2 5l2 2 4-5" fill="none" stroke="#333" stroke-width="1.3"/></svg></span>
  </div>

  <div class="login-panel">
    <div class="panel-tab">LOGIN</div>
    <svg class="panel-close" width="8" height="8" viewBox="0 0 8 8"><path d="M1 1l6 6M7 1L1 7" stroke="#6a4a6a" stroke-width="1.2"/></svg>
    <span class="field-label" style="top:44px">Password:</span>
    <span class="field-input" style="top:58px"></span>
    <span class="field-label" style="top:86px">Username:</span>
    <span class="field-input" style="top:100px"></span>
    <div class="option" style="top:126px">
      <span class="check"><svg width="10" height="10" viewBox="0 0 10 10"><path d="M2 5l2 2 4-5" fill="none" stroke="#333" stroke-width="1.3"/></svg></span>
      Remember Me
    </div>
    <div class="option" style="top:146px">
      <span class="check"><svg width="10" height="10" viewBox="0 0 10 10"><path d="M2 5l2 2 4-5" fill="none" stroke="#333" stroke-width="1.3"/></svg></span>
      <span>Forgot Your Password? <a href="#">Click here</a></span>
    </div>
    <div class="submit-button">SUBMIT</div>
  </div>

  <div class="social-links">
    <span class="social-feed"></span>
    <span class="social-birds"></span>
    <span class="social-book"></span>
  </div>

  <footer class="footer-bar">
    <span>COPYRIGHT © 2011 QENTROVA. USE OF THIS WEBSITE CONSTITUTES ACCEPTANCE OF OUR&nbsp;<a href="#">USER AGREEMENT</a>&nbsp;AND&nbsp;<a href="#">PRIVACY POLICY</a>.</span>
  </footer>
</div>
</body>
</html>
```